Business Card for a mobile physiotherapy company

I need a layout for a business card for a mobile physiotherapy company.
Slogan is "Mobile Physiotherapy - Your Road To Recovery"
Phone number is 867-555-0142
Email VardenTherapy@postnest.ca (subject to change with website)
Website www.VardenTherapy.ca
My name and credentials: Luke Varden Luke Varden, BSc(kin), MPT, CAFCI, IMS
Information maybe included: Direct Billing, Services including Physiotherapy, IMS, acupuncture
Maybe include facebook and instagram logos
One side with the logo clean and sharp
Other side with details, try not to look too busy, keep everything concise

```html
<!DOCTYPE html>
<html lang="en">
<head>
<meta charset="utf-8">
<title>Varden Therapy – Business Card</title>
<link rel="stylesheet" href="https://fonts.googleapis.com/css2?family=Playfair+Display:wght@700&family=Lora:wght@400;700&family=Roboto:wght@400&display=swap">
<style>
  :root {
    --navy: #2e4a79;
    --green: #0d5a47;
    --white: #ffffff;
    --page: #e4e6ea;
    --ink-soft: #3a4f74;
  }
  * { box-sizing: border-box; margin: 0; padding: 0; }
  html, body { width: 1200px; height: 1108px; overflow: hidden; background: var(--page); }
  .canvas { position: relative; width: 1200px; height: 1108px; }

  .card {
    position: absolute; left: 150px; width: 900px; height: 514px;
    overflow: hidden; box-shadow: 0 10px 30px rgba(0,0,0,.18);
  }
  .card--front { top: 32px; background: var(--navy); color: var(--white); }
  .card--back { top: 570px; background: var(--white); }

  /* Front */
  .front-brand {
    position: absolute; left: 0; right: 0; top: 150px; text-align: center;
    font-family: "Playfair Display", Georgia, serif; font-weight: 700; color: var(--white);
  }
  .front-brand .brand-main { display: block; font-size: 84px; letter-spacing: 6px; line-height: 1; }
  .front-brand .brand-sub { display: block; font-size: 28px; letter-spacing: 22px; margin-top: 10px; padding-left: 22px; }
  .front-tagline {
    position: absolute; left: 0; right: 0; top: 330px; text-align: center;
    font-family: "Roboto", Arial, sans-serif; font-size: 22px; line-height: 1.45;
  }
  .social { position: absolute; right: 48px; top: 232px; display: flex; gap: 12px; }
  .social span { width: 34px; height: 34px; border-radius: 50%; background: var(--white); display: block; }

  /* Back */
  .back-brand {
    position: absolute; left: 70px; top: 52px;
    font-family: "Playfair Display", Georgia, serif; font-weight: 700; color: var(--green);
  }
  .back-brand .brand-main { display: block; font-size: 72px; letter-spacing: 6px; line-height: 1; }
  .back-brand .brand-sub { display: block; font-size: 26px; letter-spacing: 20px; margin-top: 8px; }
  .person { position: absolute; left: 70px; top: 176px; font-family: "Lora", Georgia, serif; }
  .person-name { font-size: 30px; font-weight: 700; color: var(--navy); letter-spacing: .5px; }
  .person-creds { font-size: 20px; color: var(--ink-soft); margin-top: 2px; }
  .person-billing { font-size: 20px; color: var(--green); margin-top: 2px; }
  .divider { width: 30px; height: 2px; background: var(--navy); margin-top: 16px; }
  .contact { position: absolute; left: 70px; top: 338px; list-style: none; font-family: "Lora", Georgia, serif; font-size: 21px; color: #333c4a; }
  .contact li { display: flex; align-items: center; gap: 12px; line-height: 34px; }
  .contact svg { width: 18px; height: 18px; fill: var(--navy); flex: none; }
  .corner-mark { position: absolute; right: 0; bottom: 0; width: 300px; height: 300px; background: var(--navy); }
</style>
</head>
<body>
<main class="canvas">
  <section class="card card--front" aria-label="Card front">
    <div class="front-brand">
      <span class="brand-main">VARDEN</span>
      <span class="brand-sub">THERAPY</span>
    </div>
    <p class="front-tagline">Mobile Physiotherapy - Your Road To Recovery<br>Physiotherapy • IMS • Acupuncture</p>
    <div class="social" aria-label="Social media links"><span></span><span></span></div>
  </section>

  <section class="card card--back" aria-label="Card back">
    <div class="back-brand">
      <span class="brand-main">VARDEN</span>
      <span class="brand-sub">THERAPY</span>
    </div>
    <div class="person">
      <p class="person-name">LUKE VARDEN</p>
      <p class="person-creds">BSc(kin), MPT, CAFCI, IMS</p>
      <p class="person-billing">Direct Billing</p>
      <div class="divider"></div>
    </div>
    <ul class="contact">
      <li><svg viewBox="0 0 24 24" aria-hidden="true"><path d="M6.6 10.8a15.1 15.1 0 0 0 6.6 6.6l2.2-2.2a1 1 0 0 1 1-.25 11.4 11.4 0 0 0 3.6.57 1 1 0 0 1 1 1V20a1 1 0 0 1-1 1A17 17 0 0 1 3 4a1 1 0 0 1 1-1h3.5a1 1 0 0 1 1 1c0 1.25.2 2.45.57 3.57a1 1 0 0 1-.25 1z"/></svg>867-555-0142</li>
      <li><svg viewBox="0 0 24 24" aria-hidden="true"><path d="M2 5h20v14H2zm2 2v.5l8 5 8-5V7zm0 2.8V17h16V9.8l-8 5z"/></svg>VardenTherapy@postnest.ca</li>
      <li><svg viewBox="0 0 24 24" aria-hidden="true"><path d="M12 2a10 10 0 1 0 0 20 10 10 0 0 0 0-20zm0 2a8 8 0 0 1 7.7 6H16a13 13 0 0 0-1.7-5.7A8 8 0 0 1 12 4zm-2 .3A13 13 0 0 0 8 10H4.3A8 8 0 0 1 10 4.3zM4.3 14H8a13 13 0 0 0 2 5.7A8 8 0 0 1 4.3 14zm5.7 0h4a11 11 0 0 1-2 5.5A11 11 0 0 1 10 14zm0-4a11 11 0 0 1 2-5.5 11 11 0 0 1 2 5.5zm4.3 9.7A13 13 0 0 0 16 14h3.7a8 8 0 0 1-5.4 5.7z"/></svg>www.VardenTherapy.ca</li>
    </ul>
    <div class="corner-mark" role="img" aria-label="Brand mark decoration in navy"></div>
  </section>
</main>
</body>
</html>
```